RWT Fittings Ltd Business Cards

We need a business card with our business logo. We provide window and door installations on high-rises in west coast British Colombia, Canada.

I would like my business information and details on one side of the card, and the other side the company name with logo

Target Market(s)

General Contractors

Industry/Entity Type

Construction

Contact Information for Business Card

one side i want my company name and logo in the dark theme logo that i provided

Requirements
Must have
• Marco Peltieri, 16045518293, RWTFittings@mailbox-demo.com, 1407-5194 Linden Row Burnaby BC, V5H 2K9, Owner & Manager

```html
<!DOCTYPE html>
<html lang="en">
<head>
<meta charset="utf-8">
<title>RWT Fittings Ltd Business Cards</title>
<link rel="stylesheet" href="https://fonts.googleapis.com/css2?family=Montserrat:wght@600;700;800&family=Roboto:wght@400;500&display=swap">
<style>
  :root {
    --stage: #222222;
    --card-white: #ffffff;
    --brand-blue: #27a9e1;
    --brand-grey: #8c8c8c;
    --ink: #1e1e1e;
    --band-grey: #efefef;
    --tint-blue: #e4f1fb;
    --back-grey: #8e8e8e;
    --back-grey-light: #a3a3a3;
  }
  * { box-sizing: border-box; margin: 0; padding: 0; }
  html, body { width: 1200px; height: 780px; overflow: hidden; }
  body {
    background: var(--stage);
    font-family: "Roboto", Arial, sans-serif;
    position: relative;
  }
  .card {
    position: absolute;
    top: 236px;
    width: 540px;
    height: 309px;
    overflow: hidden;
  }
  .card--front { left: 30px; background: var(--card-white); }
  .card--back  { left: 630px; }

  /* front */
  .front__wordmark {
    position: absolute;
    top: 28px;
    right: 30px;
    display: flex;
    align-items: center;
    gap: 10px;
    font-family: "Montserrat", Arial, sans-serif;
    font-weight: 800;
    font-size: 30px;
    color: var(--brand-blue);
    letter-spacing: 0.5px;
  }
  .front__wordmark-square {
    width: 26px; height: 26px;
    background: var(--brand-grey);
  }
  .front__band {
    position: absolute;
    background: var(--band-grey);
  }
  .front__band--low  { left: 0; bottom: 0; width: 260px; height: 96px; }
  .front__band--high { left: 120px; bottom: 96px; width: 140px; height: 40px; }
  .front__tint {
    position: absolute;
    right: 0;
    bottom: 0;
    width: 300px;
    height: 190px;
    background: linear-gradient(160deg, var(--tint-blue), rgba(228,241,251,0.5));
  }
  .front__accent {
    position: absolute;
    left: 0;
    top: 188px;
    width: 20px;
    height: 40px;
    background: var(--brand-blue);
  }
  .front__details {
    position: absolute;
    left: 34px;
    top: 150px;
  }
  .person__name {
    font-family: "Montserrat", Arial, sans-serif;
    font-weight: 800;
    font-size: 30px;
    line-height: 1;
  }
  .person__first { color: var(--brand-blue); }
  .person__last { color: var(--brand-grey); }
  .person__role {
    font-family: "Montserrat", Arial, sans-serif;
    font-weight: 700;
    font-size: 13px;
    color: var(--ink);
    margin-top: 4px;
  }
  .contact__address {
    font-size: 14px;
    line-height: 1.3;
    color: var(--ink);
    margin-top: 12px;
    font-style: normal;
  }
  .contact__list { list-style: none; margin-top: 10px; }
  .contact__item {
    display: flex;
    align-items: center;
    gap: 8px;
    font-size: 14px;
    line-height: 1.45;
    color: var(--ink);
  }
  .contact__icon { width: 16px; height: 16px; flex: none; }

  /* back */
  .back__surface {
    position: absolute;
    inset: 0;
    background: radial-gradient(circle at 30% 20%, var(--back-grey-light), var(--back-grey) 70%);
  }
  .back__wordmark {
    position: absolute;
    right: 70px;
    top: 150px;
    display: flex;
    align-items: center;
    gap: 8px;
    font-family: "Montserrat", Arial, sans-serif;
    font-weight: 800;
    font-size: 20px;
    color: var(--card-white);
  }
  .back__wordmark-square { width: 16px; height: 16px; background: var(--card-white); }
</style>
</head>
<body>

<section class="card card--front" aria-label="Business card front">
  <div class="front__band front__band--low"></div>
  <div class="front__band front__band--high"></div>
  <div class="front__tint" role="img" aria-label="Faint company emblem decoration"></div>

  <div class="front__wordmark">
    <span class="front__wordmark-square"></span>
    <span>RWT Fittings Ltd</span>
  </div>

  <div class="front__accent"></div>

  <div class="front__details">
    <h1 class="person__name"><span class="person__first">Marco</span> <span class="person__last">Peltieri</span></h1>
    <p class="person__role">Owner &amp; Manager</p>
    <address class="contact__address">1407-5194 Linden Row<br>Burnaby BC, V5H 2K9</address>
    <ul class="contact__list">
      <li class="contact__item">
        <svg class="contact__icon" viewBox="0 0 24 24" aria-hidden="true"><path fill="#27a9e1" d="M6.6 10.8a15 15 0 0 0 6.6 6.6l2.2-2.2a1 1 0 0 1 1-.25 11.4 11.4 0 0 0 3.6.57 1 1 0 0 1 1 1V20a1 1 0 0 1-1 1A17 17 0 0 1 3 4a1 1 0 0 1 1-1h3.5a1 1 0 0 1 1 1c0 1.25.2 2.45.57 3.57a1 1 0 0 1-.25 1z"/></svg>
        <span>1604 551 8293</span>
      </li>
      <li class="contact__item">
        <svg class="contact__icon" viewBox="0 0 24 24" aria-hidden="true"><rect x="2" y="5" width="20" height="14" rx="1.5" fill="#27a9e1"/><path d="M3 6.5l9 6.5 9-6.5" fill="none" stroke="#fff" stroke-width="1.6"/></svg>
        <span>RWTFittings@mailbox-demo.com</span>
      </li>
    </ul>
  </div>
</section>

<section class="card card--back" aria-label="Business card back">
  <div class="back__surface" role="img" aria-label="Grey embossed repeating emblem pattern"></div>
  <div class="back__wordmark">
    <span class="back__wordmark-square"></span>
    <span>RWT Fittings Ltd</span>
  </div>
</section>

</body>
</html>
```